Meadowlark Property Review is a leading provider of residential appraisal and home inspection products in S

I need a business card/logo designed that obviously describes my business. We are a residential appraisal and home inspection company in Springfield, MO. We offer residential appraisals, home inspection, pest inspection and radon gas measurement. We have been in business for 18 years and hold state certified residential appraisal licenses and OBREX certified home inspection licenses. I have a logo that I really like and will attach, but would be open to new suggestions. I like more modern designs than traditional and would like a two sided card with our services, licenses and qualifications on the back.

```html
<!DOCTYPE html>
<html lang="en">
<head>
<meta charset="utf-8">
<title>Meadowlark Property Review – Business Card</title>
<link rel="stylesheet" href="https://fonts.googleapis.com/css2?family=PT+Sans:ital,wght@0,400;0,700;1,400&display=swap">
<style>
  :root {
    --page-bg: #d9d4ce;
    --card-top: #f1efec;
    --card-mid: #e4e1dd;
    --band-dark: #3f2c23;
    --band-light: #6a4c3d;
    --accent: #e2691f;
    --brand: #4a3329;
    --text-light: #f3ebe5;
    --text-soft: #e6d8cf;
    --divider: rgba(243, 235, 229, 0.55);
  }
  * { margin: 0; padding: 0; box-sizing: border-box; }
  html, body {
    width: 1200px;
    height: 969px;
    overflow: hidden;
    background: var(--page-bg);
    font-family: "PT Sans", Arial, sans-serif;
  }
  .card {
    position: absolute;
    left: 100px;
    top: 202px;
    width: 1000px;
    height: 564px;
    border-radius: 26px;
    overflow: hidden;
    background: linear-gradient(180deg, var(--card-top) 0%, var(--card-mid) 100%);
    box-shadow: 0 18px 40px rgba(60, 40, 30, 0.22);
  }
  .card-shapes {
    position: absolute;
    inset: 0;
  }
  .brand-name {
    position: absolute;
    left: 0;
    right: 0;
    top: 140px;
    text-align: center;
    font-weight: 700;
    font-size: 50px;
    letter-spacing: 3px;
    color: var(--brand);
    text-transform: uppercase;
  }
  .identity {
    position: absolute;
    right: 558px;
    top: 345px;
    text-align: right;
    color: var(--text-light);
  }
  .identity .person-name {
    font-size: 31px;
    color: var(--accent);
    line-height: 38px;
  }
  .identity .line {
    font-size: 24px;
    line-height: 38px;
  }
  .divider {
    position: absolute;
    left: 482px;
    top: 348px;
    width: 2px;
    height: 148px;
    background: var(--divider);
  }
  .contacts {
    position: absolute;
    left: 530px;
    top: 345px;
    list-style: none;
  }
  .contacts li {
    display: flex;
    align-items: center;
    height: 38px;
    font-size: 23px;
    color: var(--text-soft);
  }
  .contacts svg {
    width: 22px;
    height: 22px;
    margin-right: 14px;
    fill: var(--accent);
    flex: none;
  }
  .services {
    position: absolute;
    left: 0;
    right: 0;
    top: 516px;
    text-align: center;
    font-style: italic;
    font-size: 23px;
    color: var(--text-soft);
  }
</style>
</head>
<body>
  <div class="card">
    <svg class="card-shapes" viewBox="0 0 1000 564" preserveAspectRatio="none" aria-hidden="true">
      <defs>
        <linearGradient id="bandFill" x1="0" y1="0" x2="0" y2="1">
          <stop offset="0" stop-color="var(--band-light)"/>
          <stop offset="1" stop-color="var(--band-dark)"/>
        </linearGradient>
      </defs>
      <path d="M0 335 Q500 262 1000 335 L1000 564 L0 564 Z" fill="url(#bandFill)"/>
      <path d="M95 316 Q500 262 905 316" fill="none" stroke="var(--accent)" stroke-width="5" stroke-linecap="round"/>
    </svg>

    <div class="brand-name">Meadowlark Property Review</div>

    <div class="identity">
      <div class="person-name">Daniel Hart</div>
      <div class="line">CEO/Founder</div>
      <div class="line">1420 Walnut Ridge Drive</div>
      <div class="line">Springfield, Missouri 65804</div>
    </div>

    <div class="divider"></div>

    <ul class="contacts">
      <li>
        <svg viewBox="0 0 24 24"><path d="M6.6 10.8a15.1 15.1 0 0 0 6.6 6.6l2.2-2.2a1 1 0 0 1 1-.25 11.4 11.4 0 0 0 3.6.57 1 1 0 0 1 1 1V20a1 1 0 0 1-1 1A17 17 0 0 1 3 4a1 1 0 0 1 1-1h3.5a1 1 0 0 1 1 1c0 1.25.2 2.45.57 3.57a1 1 0 0 1-.25 1z"/></svg>
        417 555 0182
      </li>
      <li>
        <svg viewBox="0 0 24 24"><path d="M6 2h12v5H6z M4 8h16a2 2 0 0 1 2 2v7h-4v5H6v-5H2v-7a2 2 0 0 1 2-2z M8 15v5h8v-5z"/></svg>
        417 555 0193
      </li>
      <li>
        <svg viewBox="0 0 24 24"><path d="M2 5h20v14H2z M3.5 6.5 12 13l8.5-6.5v-.1H3.5z" fill-rule="evenodd"/></svg>
        daniel@meadowlarkreview.com
      </li>
      <li>
        <svg viewBox="0 0 24 24"><path d="M12 2a10 10 0 1 0 0 20 10 10 0 0 0 0-20zm6.9 6h-3a15 15 0 0 0-1.4-3.9A8 8 0 0 1 18.9 8zM12 4a13 13 0 0 1 1.9 4h-3.8A13 13 0 0 1 12 4zM4.3 14a8 8 0 0 1 0-4h3.4a16 16 0 0 0 0 4zm.8 2h3a15 15 0 0 0 1.4 3.9A8 8 0 0 1 5.1 16zm3-8h-3a8 8 0 0 1 4.4-3.9A15 15 0 0 0 8.1 8zM12 20a13 13 0 0 1-1.9-4h3.8A13 13 0 0 1 12 20zm2.3-6H9.7a14 14 0 0 1 0-4h4.6a14 14 0 0 1 0 4zm.2 5.9a15 15 0 0 0 1.4-3.9h3a8 8 0 0 1-4.4 3.9zm1.8-5.9a16 16 0 0 0 0-4h3.4a8 8 0 0 1 0 4z"/></svg>
        www.meadowlarkreview.com
      </li>
    </ul>

    <p class="services">Residential appraisals | Home inspection | Pest inspection &amp; radon gas measurement.</p>
  </div>
</body>
</html>
```